I have a business that exists already (Linden Conservatory of Music) that we offer music lessons to all instruments. I recently opened a smaller version called CHORDS by Linden that will only teach piano lessons. What I'm looking for now is a 3 page Website on word press. After I choose the design I like I want to be able to take over the website and bring it to our hosting company. We want full control of it and our team will take over. The reason I'm doing this is to have other visions and ideas from others. The first page will be about the company and our message/vision. Second page about the piano lessons. The third will be about franchising this concept "Chords by Linden" Attached are 3 Logos . Please refer to our existing website www.lindenmusicconservatory.example to look at our piano page and franchising page. Please feel free to message me if you need more info. Thanks
Please note I do not want the new website (Chords by Linden) To look like the other Website (Linden Conservatory of Music) Fresh new look. I do not want the colours red or using the Red logo. I only provided it so that you have an Idea of What the other business looks like and that you can take the piano content and franchise content off of it. Chords by Linden is smaller concept and only piano lessons.
Thanks
Only Piano lessons for all students
3 page

```html
<!DOCTYPE html>
<html lang="en">
<head>
<meta charset="utf-8">
<title>CHORDS by Linden — Piano Lessons</title>
<link href="https://fonts.googleapis.com/css2?family=Lora:ital,wght@0,400;0,500;0,700;1,400&family=Great+Vibes&family=Montserrat:wght@400;500&display=swap" rel="stylesheet">
<style>
:root{
  --teal:#5bc5b9;
  --gold:#e6c45f;
  --ink:#222;
  --text:#333;
  --sand:#f0efeb;
  --black:#000;
  --white:#fff;
}
*{margin:0;padding:0;box-sizing:border-box}
html,body{width:1200px;height:2904px;overflow:hidden}
body{position:relative;background:var(--white);font-family:'Lora',serif;color:var(--text)}
a{text-decoration:none}

/* header */
.site-header{position:absolute;left:0;top:0;width:1200px;height:81px;background:var(--black);z-index:2}
.brand{position:absolute;left:152px;top:16px;color:var(--white);font-family:'Lora',serif;font-size:30px;line-height:32px;letter-spacing:1px}
.brand small{display:block;font-size:13px;line-height:14px;letter-spacing:1px;color:var(--white);margin-left:34px}
.nav{position:absolute;top:33px;font-size:13px;color:var(--white);text-transform:uppercase;letter-spacing:.3px}
.nav.active{color:var(--gold)}
.nav-sep{position:absolute;left:972px;top:24px;width:1px;height:34px;background:#666}
.social-dot{position:absolute;top:35px;width:12px;height:12px;border-radius:50%;background:var(--gold)}

/* hero */
.hero{position:absolute;left:0;top:81px;width:1200px;height:551px;
  background:linear-gradient(100deg,#0b0908 0%,#1a1310 30%,#3a2417 55%,#6b4a2c 75%,#2a1d14 100%)}
.hero-script{position:absolute;left:149px;top:232px;font-family:'Great Vibes',cursive;font-size:66px;color:var(--gold);line-height:1}
.hero-title{position:absolute;left:149px;top:318px;font-family:'Lora',serif;font-size:56px;font-weight:400;color:var(--white);letter-spacing:.5px;line-height:1}
.btn{position:absolute;display:flex;align-items:center;justify-content:center;font-family:'Lora',serif;text-transform:uppercase;font-size:13px;letter-spacing:.4px}
.btn-gold{background:var(--gold);color:#111;border-radius:2px}
.btn-teal{background:var(--teal);color:var(--white);font-weight:700}

/* intro */
.intro{position:absolute;left:0;top:632px;width:1200px;height:572px;background:var(--sand)}
.photo{position:absolute}
.intro-card{position:absolute;left:579px;top:19px;width:479px;height:422px;background:var(--white);text-align:center;padding:44px 38px 0}
.intro-card h2{font-weight:400;font-size:34px;color:var(--ink);margin-bottom:18px}
.intro-card p{font-size:13px;line-height:23px;color:var(--ink);margin-bottom:5px}
.down-mark{position:absolute;left:579px;top:481px}

/* vision */
.vision{position:absolute;left:143px;top:1310px;width:500px}
.vision h2{font-weight:400;font-size:34px;line-height:44px;color:var(--ink);margin-bottom:8px}
.body-copy{font-size:13px;line-height:25.5px;color:var(--ink)}
.body-copy p{margin-bottom:7px}
.vision .btn{position:relative;margin-left:-2px;margin-top:10px;width:169px;height:35px}

/* programs */
.section-title{position:absolute;font-weight:400;color:var(--ink)}
.frame{position:absolute;background:var(--teal)}
.frame-line{position:absolute;border:2px solid var(--white)}
.checklist{position:absolute;left:576px;top:1812px;width:480px;list-style:none;font-size:14px;line-height:22.5px;color:var(--ink)}
.checklist li{position:relative;padding-left:25px;margin-bottom:9px}
.checklist svg{position:absolute;left:2px;top:6px}

/* quote */
.quote-card{position:absolute;left:141px;top:2209px;width:917px;height:211px;background:var(--white);border-radius:20px;box-shadow:0 4px 22px rgba(0,0,0,.1);text-align:center}
.quote-card blockquote{position:absolute;left:150px;top:44px;width:627px;font-style:italic;font-size:22px;line-height:38px;color:var(--ink)}
.quote-card cite{position:absolute;left:0;top:135px;width:100%;font-style:normal;font-size:18px;color:var(--teal);letter-spacing:.6px}
.quote-mark{position:absolute;left:84px;top:16px;font-family:'Lora',serif;font-size:150px;color:#eee;line-height:1}

/* franchise */
.franchise-title{position:absolute;left:0;top:2490px;width:1200px;text-align:center;font-size:45px;font-weight:400;color:var(--ink)}
.franchise-sub{position:absolute;left:0;top:2559px;width:1200px;text-align:center;font-size:21px;color:var(--ink);text-transform:uppercase}

/* footer */
.site-footer{position:absolute;left:0;top:2707px;width:1200px;height:150px;background:var(--black);color:var(--white)}
.contact-item{position:absolute;top:50px;display:flex;align-items:center;color:var(--white)}
.contact-item .label{font-size:14px;line-height:18px}
.contact-item .value{font-size:19px;line-height:24px}
.contact-item .small{font-size:12.5px;line-height:19px;color:var(--white)}
.contact-item strong{font-size:13.5px;font-weight:700;display:block;line-height:18px}
.contact-icon{width:40px;height:40px;border:2px solid var(--white);border-radius:50%;display:flex;align-items:center;justify-content:center;margin-right:16px;flex:none}
.footer-sep{position:absolute;top:52px;width:1px;height:30px;background:#555}
.copyright-bar{position:absolute;left:0;top:2857px;width:1200px;height:47px;background:var(--teal)}
.copyright-bar p{position:absolute;left:143px;top:16px;font-family:'Montserrat',sans-serif;font-size:12.5px;color:var(--white)}
.bar-dot{position:absolute;top:12px;width:25px;height:25px;border:1.5px solid var(--white);border-radius:50%}
</style>
</head>
<body>

<header class="site-header">
  <div class="brand">CHORDS<small>by Linden</small></div>
  <span class="nav active" style="left:485px">Home</span>
  <span class="nav" style="left:573px">Piano Lessons</span>
  <span class="nav" style="left:721px">Franchising</span>
  <span class="nav" style="left:855px">Contact Us</span>
  <span class="nav-sep"></span>
  <span class="social-dot" style="left:1002px"></span>
  <span class="social-dot" style="left:1036px"></span>
  <span class="social-dot" style="left:1072px"></span>
  <span class="social-dot" style="left:1105px"></span>
</header>

<section class="hero" role="img" aria-label="Young woman playing a grand piano on a dimly lit stage"></section>
<div class="hero-script">Welcome to</div>
<h1 class="hero-title">CHORDS BY LINDEN</h1>
<a class="btn btn-gold" style="left:149px;top:411px;width:121px;height:36px">Read More</a>

<section class="intro">
  <div class="photo" role="img" aria-label="Close-up of a student's hands on piano keys guided by a teacher" style="left:141px;top:19px;width:438px;height:422px;background:linear-gradient(135deg,#d9dcd8 0%,#a9aeaa 40%,#2e3130 70%,#111 100%)"></div>
  <div class="intro-card">
    <h2>Playing The Piano</h2>
    <p>When you think of a piano, you probably envision black and white keys but the piano is more than those harmonious sounds created by the player.</p>
    <p>The versatility and the musicianship instilled into the player from those keys is the true magic that comes from playing piano! Starting from the grassroots, experience different methods and styles of playing piano. To mark the milestones of progression, engage in one of Linden’s many unique performance opportunities like annual festival competitions, recitals or our examinations (Linden &amp; NPB). Penultimately, at the end of the journey, join our elite teaching program to bring the same joy of learning the piano to another student.</p>
  </div>
  <svg class="down-mark" width="42" height="42" viewBox="0 0 42 42" aria-hidden="true">
    <rect x="7" y="7" width="28" height="28" transform="rotate(45 21 21)" fill="none" stroke="#d5d3ce" stroke-width="1.5"/>
    <path d="M21 14v13M16 23l5 5 5-5" fill="none" stroke="#c5c3be" stroke-width="1.5"/>
  </svg>
</section>

<section class="vision">
  <h2>Our Vision</h2>
  <div class="body-copy">
    <p>Lorem ipsum dolor sit amet, consectetur adipiscing elit. In hendrerit, odio utrtyy semper consequat, justo dui convallis ligula, ac congue felis ipsum sed felis. Cura volutpat leo faucibus magna elementum ultrices.</p>
    <p>Cras eleifend faucibus lacus convallis elementum. Phasellus vitae lobortis donece in risus sit amet enim eleifend semper sed id ipsum. Ut ac placerat nisl pellentesq venenatis ligula eget turpis aliquam ornare. Vivamus tincidunt tellus at rutrum fd aliquam. Etiam ullamcorper consequat felis vitae posuere. Nunc nec facilisis nuni, at dignissim augue. Sed sed orci felis. Aliquam quis auctor ipsum.</p>
  </div>
  <a class="btn btn-teal">Contact Us Today</a>
</section>

<div class="frame" style="left:741px;top:1283px;width:317px;height:319px"></div>
<div class="frame-line" style="left:741px;top:1300px;width:299px;height:302px;border-left:none;border-bottom:none"></div>
<div class="photo" role="img" aria-label="Teacher with two children at a keyboard in a bright living room" style="left:678px;top:1345px;width:318px;height:316px;background:linear-gradient(160deg,#f3ece4 0%,#e8d3c2 45%,#f2a38e 70%,#d7b7c4 100%)"></div>

<div class="frame" style="left:142px;top:1727px;width:317px;height:319px"></div>
<div class="frame-line" style="left:160px;top:1745px;width:299px;height:301px;border-right:none;border-bottom:none"></div>
<div class="photo" role="img" aria-label="Two teenage girls practising together at a piano" style="left:204px;top:1789px;width:317px;height:316px;background:linear-gradient(150deg,#f5f1ec 0%,#d9b9a0 40%,#7a5a44 65%,#2a2523 100%)"></div>

<h2 class="section-title" style="left:576px;top:1720px;width:500px;font-size:30px;line-height:40px">Our Programs Also Provide Students The Opportunity To</h2>
<ul class="checklist">
  <li><svg width="13" height="13" viewBox="0 0 13 13"><circle cx="6.5" cy="6.5" r="5.5" fill="none" stroke="#555"/><path d="M3.8 6.6l2 2 4-4.5" fill="none" stroke="#555" stroke-width="1.3"/></svg>Participate in large-scale performances.</li>
  <li><svg width="13" height="13" viewBox="0 0 13 13"><circle cx="6.5" cy="6.5" r="5.5" fill="none" stroke="#555"/><path d="M3.8 6.6l2 2 4-4.5" fill="none" stroke="#555" stroke-width="1.3"/></svg>Perform at Linden’s many community events on a regular basis.</li>
  <li><svg width="13" height="13" viewBox="0 0 13 13"><circle cx="6.5" cy="6.5" r="5.5" fill="none" stroke="#555"/><path d="M3.8 6.6l2 2 4-4.5" fill="none" stroke="#555" stroke-width="1.3"/></svg>Access the GTA’s coolest Broadcast stage</li>
  <li><svg width="13" height="13" viewBox="0 0 13 13"><circle cx="6.5" cy="6.5" r="5.5" fill="none" stroke="#555"/><path d="M3.8 6.6l2 2 4-4.5" fill="none" stroke="#555" stroke-width="1.3"/></svg>Attend Clinics, Masterclasses, and Jam Nights</li>
  <li><svg width="13" height="13" viewBox="0 0 13 13"><circle cx="6.5" cy="6.5" r="5.5" fill="none" stroke="#555"/><path d="M3.8 6.6l2 2 4-4.5" fill="none" stroke="#555" stroke-width="1.3"/></svg>Access the Linden Rocks band program. Linden’s Band Program empowers and electrifies students to come together, create music and confidently hit the stage with their own band identity while having fun and honing their instrument.</li>
  <li><svg width="13" height="13" viewBox="0 0 13 13"><circle cx="6.5" cy="6.5" r="5.5" fill="none" stroke="#555"/><path d="M3.8 6.6l2 2 4-4.5" fill="none" stroke="#555" stroke-width="1.3"/></svg>Register in our elite teaching program to learn how to pass on the magic and passion of playing the piano to students.</li>
</ul>
<a class="btn btn-teal" style="left:575px;top:2103px;width:170px;height:35px">Contact Us Today</a>

<section class="quote-card">
  <span class="quote-mark">“</span>
  <blockquote>“Life is like a piano. What you get out of it depends on how you play it.”</blockquote>
  <cite>MARION VALE</cite>
</section>

<h2 class="franchise-title">Franchise Opportunities</h2>
<p class="franchise-sub">Be part of the Linden Conservatory family</p>
<a class="btn btn-teal" style="left:530px;top:2602px;width:141px;height:34px">Know More</a>

<footer class="site-footer">
  <div class="contact-item" style="left:190px">
    <span class="contact-icon"><svg width="20" height="20" viewBox="0 0 24 24"><path d="M6.6 10.8c1.4 2.8 3.8 5.1 6.6 6.6l2.2-2.2c.3-.3.7-.4 1-.2 1.1.4 2.3.6 3.6.6.6 0 1 .4 1 1V20c0 .6-.4 1-1 1C10.6 21 3 13.4 3 4c0-.6.4-1 1-1h3.5c.6 0 1 .4 1 1 0 1.3.2 2.5.6 3.6.1.3 0 .7-.2 1z" fill="#fff"/></svg></span>
    <div><div class="label">Call Us Now</div><div class="value">1-888-555-0147</div></div>
  </div>
  <span class="footer-sep" style="left:443px"></span>
  <div class="contact-item" style="left:478px;top:46px">
    <span class="contact-icon"><svg width="18" height="20" viewBox="0 0 24 24"><path d="M12 2C8.1 2 5 5.1 5 9c0 5.2 7 13 7 13s7-7.8 7-13c0-3.9-3.1-7-7-7zm0 9.5a2.5 2.5 0 110-5 2.5 2.5 0 010 5z" fill="#fff"/></svg></span>
    <div><strong>CHORDS LINDEN</strong><div class="small">48 Elm Court, Suite 2, Main Street<br>Halton Hills ON 100482</div></div>
  </div>
  <span class="footer-sep" style="left:757px"></span>
  <div class="contact-item" style="left:814px">
    <span class="contact-icon"><svg width="18" height="16" viewBox="0 0 24 20"><rect x="1" y="2" width="22" height="16" rx="2" fill="#fff"/><path d="M2 4l10 7 10-7" fill="none" stroke="#000" stroke-width="2"/></svg></span>
    <div><div class="label">Email Us:</div><div class="small" style="font-size:13.5px">hello@chordslinden.example</div></div>
  </div>
</footer>

<div class="copyright-bar">
  <p>Copyright © 2020 CHORDS LINDEN. All Rights Reserved.</p>
  <span class="bar-dot" style="left:940px"></span>
  <span class="bar-dot" style="left:971px"></span>
  <span class="bar-dot" style="left:1002px"></span>
  <span class="bar-dot" style="left:1034px"></span>
</div>

</body>
</html>
```